BRISK requires an exciting new business card

New business card required for BRISK. We are a new market research consultancy and want our brand to be approachable and be contemporary/modern, bold, uncomplicated/simple, and use friendly and easy to read fonts.

A draft website front page is attached to give you a feel (the pictures will be improved over the coming days).

The business card will be printed on 600gsm card, full colour both sides. The card is unique in that it allows one of four colours to be placed within the seam of the card (see http://uk.prentvo.com/products/gilt/business-cards.html)

The logo has been designed in yellow on white, white on yellow, yellow on black and black on yellow - please select whichever you feel most appropriate from the attached document (please use the versions with the tagline). I think my preference is yellow on white for the front, and then yellow or black as the dominant colour on the back.

Telephone numbers will be given next week as they are now being finalised.

Thanks

Target Market(s)

Professionals in large corporates, such as Marketing Managers at Grovane, Fizzaro Pop, Delmarco etc.

Industry/Entity Type

Market Research

Requirements
Must have
• Dana Pruitt QPMR
brisk
Level 4, 37 Quarrell St
Surrey Hills
NSW 2010
Tel: 02 XXXX XXXX
Mob: XXXX XXXXXX
Email: dana@briskqr.com.au
Web: www.briskqr.com.au

```html
<!DOCTYPE html>
<html lang="en">
<head>
<meta charset="utf-8">
<title>BRISK business card</title>
<link rel="stylesheet" href="https://fonts.googleapis.com/css2?family=Jost:wght@400;500;700&display=swap">
<style>
  :root {
    --brand-yellow: #ffcc00;
    --ink: #3d3d3d;
    --rule: #9a9a9a;
    --paper: #ffffff;
    --backdrop: #e4e4ea;
  }
  html, body {
    margin: 0;
    padding: 0;
    width: 1200px;
    height: 987px;
    overflow: hidden;
    background: var(--backdrop);
    font-family: "Jost", sans-serif;
  }
  .canvas {
    position: relative;
    width: 1200px;
    height: 987px;
  }
  .card {
    position: absolute;
    left: 220px;
    width: 760px;
    height: 440px;
    background: var(--paper);
    border-radius: 28px;
    overflow: hidden;
    box-shadow: 0 6px 18px rgba(0,0,0,0.12);
  }
  .card--front { top: 34px; }
  .card--back { top: 512px; }

  /* front */
  .front-lockup {
    position: absolute;
    left: 90px;
    top: 40px;
  }
  .front-wordmark {
    display: block;
    font-size: 230px;
    font-weight: 700;
    line-height: 1;
    letter-spacing: -6px;
    color: var(--brand-yellow);
  }
  .front-tagline {
    display: block;
    margin-top: -18px;
    padding-left: 10px;
    font-size: 38px;
    font-weight: 400;
    color: var(--ink);
  }
  .front-url {
    display: block;
    margin-top: 14px;
    padding-left: 14px;
    font-size: 26px;
    letter-spacing: 7px;
    color: var(--ink);
  }

  /* back */
  .back-lockup {
    position: absolute;
    left: 44px;
    top: 30px;
  }
  .back-wordmark {
    display: block;
    font-size: 120px;
    font-weight: 700;
    line-height: 1;
    letter-spacing: -3px;
    color: var(--brand-yellow);
  }
  .back-tagline {
    display: block;
    margin-top: -6px;
    padding-left: 6px;
    font-size: 20px;
    color: var(--ink);
  }
  .divider {
    position: absolute;
    left: 392px;
    top: 40px;
    width: 1px;
    height: 240px;
    background: var(--rule);
  }
  .contact {
    position: absolute;
    left: 420px;
    top: 48px;
    color: var(--ink);
  }
  .contact-name {
    margin: 0 0 14px;
    font-size: 28px;
    font-weight: 500;
    color: var(--brand-yellow);
  }
  .contact-list {
    list-style: none;
    margin: 0;
    padding: 0;
    font-size: 25px;
    line-height: 1.35;
  }
  .contact-list li {
    display: flex;
    align-items: center;
    gap: 10px;
  }
  .contact-icon {
    width: 18px;
    height: 18px;
    flex: none;
  }
  .address-band {
    position: absolute;
    left: 0;
    right: 0;
    top: 318px;
    height: 62px;
    background: var(--brand-yellow);
    display: flex;
    align-items: center;
    padding-left: 44px;
    font-size: 26px;
    font-weight: 500;
    color: var(--ink);
  }
  .band-rule {
    position: absolute;
    left: 0;
    right: 0;
    height: 1px;
    background: var(--rule);
  }
  .band-rule--top { top: 306px; }
  .band-rule--bottom { top: 392px; }
</style>
</head>
<body>
<main class="canvas">

  <section class="card card--front" aria-label="Card front">
    <div class="front-lockup">
      <span class="front-wordmark">brisk</span>
      <span class="front-tagline">considered insights</span>
      <span class="front-url">www.briskqr.com.au</span>
    </div>
  </section>

  <section class="card card--back" aria-label="Card back">
    <div class="back-lockup">
      <span class="back-wordmark">brisk</span>
      <span class="back-tagline">considered insights</span>
    </div>

    <div class="divider"></div>

    <div class="contact">
      <p class="contact-name">Dana Pruitt QPMR</p>
      <ul class="contact-list">
        <li>
          <svg class="contact-icon" viewBox="0 0 20 20"><circle cx="10" cy="10" r="10" fill="var(--brand-yellow)"/><path d="M6 5c1 0 1.5 2 1 3l-1 1c1 2 2 3 4 4l1-1c1-.5 3 0 3 1s-1 2-2 2C8 15 5 12 5 7c0-1 0-2 1-2z" fill="#fff"/></svg>
          03 9182 4407
        </li>
        <li>
          <svg class="contact-icon" viewBox="0 0 20 20"><rect x="5" y="1" width="10" height="18" rx="2" fill="var(--brand-yellow)"/><rect x="7" y="4" width="6" height="9" fill="#fff"/></svg>
          0491 570 226
        </li>
        <li>
          <svg class="contact-icon" viewBox="0 0 20 20"><rect x="1" y="4" width="18" height="12" rx="2" fill="var(--brand-yellow)"/><path d="M2 5l8 6 8-6" fill="none" stroke="#fff" stroke-width="1.5"/></svg>
          dana@briskqr.com.au
        </li>
        <li>
          <svg class="contact-icon" viewBox="0 0 20 20"><circle cx="10" cy="10" r="9" fill="var(--brand-yellow)"/><g fill="none" stroke="#fff" stroke-width="1.2"><ellipse cx="10" cy="10" rx="4" ry="9"/><path d="M1 10h18M3 5h14M3 15h14"/></g></svg>
          www.briskqr.com.au
        </li>
      </ul>
    </div>

    <div class="band-rule band-rule--top"></div>
    <div class="address-band">Level 4, 37 Quarrell St, Brackenvale, NSW 2291</div>
    <div class="band-rule band-rule--bottom"></div>
  </section>

</main>
</body>
</html>
```